Business Card Design Project

We need a business card for a new technology services company. We develop software and implement software packages for our business customers and although we will begin with just one or two service offerings, our service offerings will expand over time. Our name comes from the an author, KL Barrow, and his "idea" was that opportunity should be based on ability and achievement, not on social status.

We would like to see a design that is standard in its size and shape, but stands apart in its dramatic color contrasts. The card should not use too many colors - the colors used in the background should highlight the brilliant blues of the logo (see attachment) to dramatic effect. The background should not be white.

If necessary, you can change the color of the words "KL Barrow", but not the word "Idea".

Card size should be U.S. standard 2 inches by 3.5 inches and provide for 1/8 inch bleed area on each side.

We need a design for both sides of the business card, one side communicating the company logo and contact information, the other side being purely graphical, incorporating the logo but no other information.

Contact Information Required:
Kate Brook
KateBrook@klbarrowvista.com
614-387-2259

Target Market(s)

Business executives

Industry/Entity Type

Software

Requirements
Must have
• It must have the full company logo on one side, and at least the graphic element of the logo on the other. Either that or the full logo on both.
Nice to have
• It would be nice to have a design that could work without needing two different textures. For example, it would be nice if the entire card could be shiny, not just parts of the card.

It would also be nice if texture is something we could add later.
Should not have
• The card should not use the color green.

```html
<!DOCTYPE html>
<html lang="en">
<head>
<meta charset="utf-8">
<title>Corvane Labs — Business Card</title>
<link rel="stylesheet" href="https://fonts.googleapis.com/css2?family=Arimo:wght@400;700&display=swap">
<style>
  :root {
    --backdrop: #e4e1e6;
    --card-deep: #241c2c;
    --card-mid: #342a3e;
    --card-light: #43394d;
    --brand-blue: #1a9fe0;
    --wordmark-grey: #a9a6ad;
    --contact-white: #f2f0f4;
  }
  * { box-sizing: border-box; margin: 0; padding: 0; }
  html, body {
    width: 1200px;
    height: 750px;
    overflow: hidden;
  }
  body {
    background: var(--backdrop);
    font-family: "Arimo", Arial, sans-serif;
    position: relative;
  }
  .card {
    position: absolute;
    top: 220px;
    width: 540px;
    height: 309px;
    background: radial-gradient(ellipse at 45% 30%, var(--card-light) 0%, var(--card-mid) 45%, var(--card-deep) 100%);
    box-shadow: 0 8px 24px rgba(0, 0, 0, 0.25);
    overflow: hidden;
  }
  .card--front { left: 45px; }
  .card--back { left: 615px; }

  .wordmark {
    position: absolute;
    display: flex;
    align-items: center;
    gap: 16px;
  }
  .wordmark__dot {
    flex: none;
    width: 52px;
    height: 52px;
    border-radius: 50%;
    background: var(--brand-blue);
  }
  .wordmark__name {
    color: var(--wordmark-grey);
    font-weight: 400;
    font-size: 44px;
    letter-spacing: -1.5px;
    white-space: nowrap;
  }

  .card--front .wordmark { left: 66px; top: 96px; }
  .card--back .wordmark { left: 78px; top: 132px; }

  .holder-name {
    position: absolute;
    left: 66px;
    bottom: 58px;
    color: var(--brand-blue);
    font-weight: 700;
    font-size: 17px;
    letter-spacing: 0.5px;
  }
  .divider {
    position: absolute;
    left: 268px;
    bottom: 40px;
    width: 1px;
    height: 74px;
    background: var(--brand-blue);
  }
  .contact {
    position: absolute;
    left: 290px;
    bottom: 52px;
    list-style: none;
    color: var(--contact-white);
    font-size: 13.5px;
    line-height: 26px;
  }
  .contact__item {
    display: flex;
    align-items: center;
    gap: 8px;
    white-space: nowrap;
  }
  .contact__icon {
    width: 11px;
    height: 11px;
    flex: none;
  }
</style>
</head>
<body>
  <section class="card card--front" aria-label="Card front">
    <div class="wordmark">
      <span class="wordmark__name">Corvane Labs</span>
      <span class="wordmark__dot"></span>
    </div>
    <p class="holder-name">KATE BROOK</p>
    <span class="divider"></span>
    <ul class="contact">
      <li class="contact__item">
        <svg class="contact__icon" viewBox="0 0 12 12" aria-hidden="true">
          <path d="M3 1 L4.6 3.6 L3.6 4.6 Q4.8 7.2 7.4 8.4 L8.4 7.4 L11 9 L10 11 Q4 10.5 1 2 Z" fill="#ffffff"/>
        </svg>
        <span>614-387-2259</span>
      </li>
      <li class="contact__item">
        <svg class="contact__icon" viewBox="0 0 12 12" aria-hidden="true">
          <rect x="0.5" y="2.5" width="11" height="7.5" rx="1" fill="#ffffff"/>
          <path d="M0.8 3 L6 7 L11.2 3" fill="none" stroke="#342a3e" stroke-width="1.2"/>
        </svg>
        <span>KateBrook@klbarrowvista.com</span>
      </li>
    </ul>
  </section>

  <section class="card card--back" aria-label="Card back">
    <div class="wordmark">
      <span class="wordmark__name">Corvane Labs</span>
      <span class="wordmark__dot"></span>
    </div>
  </section>
</body>
</html>
```